High-end law practice specializing in closely held business succession planning and complex estates

Solo practitioner whose practice specializes in high-net worth, complex estate planning needs muliple versions of letterhead black and white, please. Letterhead should incorporate slogan, "Protecting your family business is my business," for one and "Complex Estate Planning"; third with no slogan. All for The Law Office of Marcy Lynn Pettibone, PC, 418 Cedar Hollow Ln., Newport News, Virginia 23648, Tel. 757-555-0142 Fax tbd email: marcy@mlplawgroup.example; Marcy Lynn Pettibone, Esq., principal, licensed in VA, NY, DC
Updates

Project Deadline Extended
Reason: My internet service went down and I can only view designs on my smart phone -- it's just too hard to review. So sorry! Working with my ISP now. Please be patient!

Target Market(s)

High net worth clients with complex estate planning needs, family businesses, family farmers, family foresters -- people with unique estate/succession planning needs who need a specialist who understands them.

Industry/Entity Type

Business

Font styles to use
Script

Requirements
Must have
• A high-end look and feel, connoting trustworthiness, special knowledge, and expertise.

```html
<!DOCTYPE html>
<html lang="en">
<head>
<meta charset="utf-8">
<title>The Law Office of Marcy Lynn Pettibone, PC — Letterhead</title>
<link rel="stylesheet" href="https://fonts.googleapis.com/css2?family=Tinos:ital,wght@0,400;0,700;1,400&display=swap">
<style>
  :root {
    --backdrop: #e6e4e1;
    --paper: #ffffff;
    --ink: #111111;
    --rule: #b5b5b5;
    --shadow: rgba(0, 0, 0, 0.35);
  }
  * { margin: 0; padding: 0; box-sizing: border-box; }
  html, body {
    width: 953px;
    height: 1200px;
    overflow: hidden;
    background: var(--backdrop);
  }
  .letterhead {
    position: absolute;
    left: 157px;
    top: 155px;
    width: 656px;
    height: 920px;
    background: var(--paper);
    box-shadow: 0 4px 10px var(--shadow);
    font-family: "Tinos", "Times New Roman", serif;
    color: var(--ink);
  }
  .firm-name {
    position: absolute;
    left: 35px;
    top: 27px;
    font-size: 21.5px;
    font-weight: 400;
    line-height: 24px;
    letter-spacing: 0.1px;
  }
  .attorney-line {
    position: absolute;
    left: 35px;
    top: 76px;
    font-size: 14.5px;
    line-height: 18px;
  }
  .contact {
    position: absolute;
    left: 449px;
    top: 30px;
    padding-left: 8px;
    border-left: 1px solid var(--rule);
    font-size: 11.5px;
    line-height: 13.5px;
  }
  .contact .address { margin-bottom: 5px; }
  .contact b { font-weight: 700; }
  .header-rule {
    position: absolute;
    left: 33px;
    right: 33px;
    top: 108px;
    height: 1px;
    background: var(--rule);
  }
  .footer-rule {
    position: absolute;
    left: 33px;
    right: 33px;
    top: 892px;
    height: 1px;
    background: var(--rule);
  }
  .slogan {
    position: absolute;
    left: 0;
    right: 0;
    top: 897px;
    text-align: center;
    font-style: italic;
    font-size: 15.5px;
    line-height: 18px;
  }
</style>
</head>
<body>
  <main class="letterhead">
    <header>
      <h1 class="firm-name">THE LAW OFFICE<br>OF MARCY LYNN PETTIBONE, PC</h1>
      <p class="attorney-line">Marcy Lynn Pettibone, Esq., licensed in VA, NY, DC</p>
      <address class="contact" style="font-style:normal">
        <div class="address">418 Cedar Hollow Ln.,<br>Newport News, Virginia 23648</div>
        <div><b>T</b>: 757-555-0142 | <b>F</b>: 757-555-0199</div>
        <div><b>E</b>: marcy@mlplawgroup.example</div>
      </address>
      <div class="header-rule"></div>
    </header>
    <footer>
      <div class="footer-rule"></div>
      <p class="slogan">Complex Estate Planning</p>
    </footer>
  </main>
</body>
</html>
```